Tolvik Commercial Cleaning is lookong for a new business card design.

A fresh new design that's professional and stylish. We need a serious upgrade to our business cards. I have included pictures of our existing ones. Our clients include professional individuals and business owners. We woupdblike something professional and upbeat. Please have fun and see what you come uo with.

Target Market(s)

Property managers, business owners, facility managers and other similar professionals

Industry/Entity Type

Janitorial

Contact Information for Business Card

Name, cell, office number, email, web address

Font styles to use
Sans Serif

Colors

Designer to choose colors to be used in the design.

Requirements
Must have
• please use the green color in our logo
Nice to have
• Bar code
Should not have
• Address

```html
<!DOCTYPE html>
<html lang="en">
<head>
<meta charset="UTF-8">
<title>Tolvik Commercial Cleaning – Business Card</title>
<link href="https://fonts.googleapis.com/css2?family=Figtree:wght@400;700&display=swap" rel="stylesheet">
<style>
  :root {
    --backdrop: #e4e3e1;
    --green-dark: #2b9346;
    --green-light: #46ad69;
    --brand-green: #2f9a45;
    --white: #ffffff;
    --card-light: #f3f3f3;
    --card-shade: #e6e6e6;
    --name-blue: #2e5f9c;
    --text-grey: #5a5a5a;
    --rule-grey: #6b6b6b;
  }
  * { margin: 0; padding: 0; box-sizing: border-box; }
  html, body {
    width: 1200px; height: 1200px; overflow: hidden;
    background: var(--backdrop);
    font-family: "Figtree", "Helvetica Neue", Arial, sans-serif;
  }
  .card {
    position: absolute; left: 234px;
    width: 732px; height: 418px;
  }
  .card-front {
    top: 160px;
    background: linear-gradient(225deg, var(--green-light), var(--green-dark));
    color: var(--white);
  }
  .card-back {
    top: 632px;
    background: linear-gradient(225deg, var(--card-light), var(--card-shade));
  }

  /* front */
  .front-wordmark {
    position: absolute; top: 50px; left: 0; right: 0;
    text-align: center; font-weight: 700; color: var(--white);
  }
  .front-wordmark .word { display: block; font-size: 74px; line-height: 1; letter-spacing: 1px; }
  .front-wordmark .sub { display: block; font-size: 19px; margin-top: 10px; letter-spacing: 0.5px; }
  .services-title {
    position: absolute; top: 195px; left: 0; right: 0;
    text-align: center; font-size: 30px; font-weight: 700;
  }
  .services-list {
    position: absolute; top: 248px; list-style: none;
    font-size: 20px; line-height: 32px; letter-spacing: 0.3px;
  }
  .services-list li::before {
    content: ""; display: inline-block; width: 8px; height: 8px;
    border-radius: 50%; background: var(--white);
    margin-right: 8px; vertical-align: middle; position: relative; top: -2px;
  }
  .services-left { left: 68px; }
  .services-right { left: 473px; }

  /* back */
  .back-wordmark {
    position: absolute; left: 90px; width: 244px; top: 172px;
    text-align: center; font-size: 72px; font-weight: 700;
    line-height: 1; color: var(--brand-green);
  }
  .divider {
    position: absolute; left: 369px; top: 137px;
    width: 2px; height: 143px; background: var(--rule-grey);
  }
  .person-name {
    position: absolute; left: 402px; top: 137px;
    font-size: 31px; font-weight: 700; color: var(--name-blue);
  }
  .contact-list {
    position: absolute; left: 402px; top: 195px; list-style: none;
    font-size: 20px; line-height: 28px; color: var(--text-grey);
  }
  .contact-list li { display: flex; align-items: center; }
  .contact-list svg { width: 16px; height: 16px; margin-right: 10px; fill: var(--name-blue); }
  .tagline {
    position: absolute; left: 0; right: 0; top: 360px;
    text-align: center; font-size: 20px; color: var(--brand-green); letter-spacing: 0.3px;
  }
</style>
</head>
<body>
  <section class="card card-front">
    <div class="front-wordmark">
      <span class="word">Tolvik</span>
      <span class="sub">Commercial Cleaning</span>
    </div>
    <h2 class="services-title">Services</h2>
    <ul class="services-list services-left">
      <li>Carpet Cleaning</li>
      <li>Construction Cleaning</li>
      <li>Day Labor</li>
      <li>Furniture Cleaning</li>
    </ul>
    <ul class="services-list services-right">
      <li>Power Washing</li>
      <li>VCT Cleaning</li>
      <li>Window Cleaning</li>
      <li>Furniture Cleaning</li>
    </ul>
  </section>

  <section class="card card-back">
    <div class="back-wordmark">Tolvik</div>
    <div class="divider"></div>
    <h1 class="person-name">Marisol Vance</h1>
    <ul class="contact-list">
      <li>
        <svg viewBox="0 0 24 24" aria-hidden="true"><path d="M6.6 10.8a15.1 15.1 0 0 0 6.6 6.6l2.2-2.2c.3-.3.7-.4 1-.2 1.1.4 2.3.6 3.6.6.6 0 1 .4 1 1V20c0 .6-.4 1-1 1A17 17 0 0 1 3 4c0-.6.4-1 1-1h3.5c.6 0 1 .4 1 1 0 1.3.2 2.5.6 3.6.1.3 0 .7-.2 1z"/></svg>
        (555) 014-2290
      </li>
      <li>
        <svg viewBox="0 0 24 24" aria-hidden="true"><path d="M2 5h20v2l-10 7L2 7z"/><path d="M2 9l10 7 10-7v10H2z"/></svg>
        marisol@tolvikclean.com
      </li>
      <li>
        <svg viewBox="0 0 24 24" aria-hidden="true"><circle cx="12" cy="12" r="10" fill="none" stroke="#2e5f9c" stroke-width="2.4"/><path d="M2 12h20M12 2c3 3 3 17 0 20M12 2c-3 3-3 17 0 20" fill="none" stroke="#2e5f9c" stroke-width="2"/></svg>
        www.tolvikclean.com
      </li>
    </ul>
    <p class="tagline">Care in Every Corner</p>
  </section>
</body>
</html>
```